Rice Cakes Packing Desing

We need a simple (4 color) yet colorful, atractive design for a Rice Cake polypropylene bag. We are expanding our line to include 8-10 different flavors with each bag being a different color for easy identificaction. We are starting right with the first design. We already have "sample model" (of an existing product in the usa market) upon which we believe that our design could be based on (as an idea of a simple 4 color plastic bag design), which we are including in this post. We are also including an image of Brindle Rice Cakes plastic bag that has a round front window that shows the product inside the bag, which we also would like to include in our design. We already have a brand name and a logo design. The bag's dimension is about 20cms (wide) 30cms (tall) and it will contain about 12 rice cakes inside. (I HAVE ATTACHED A COUPLE OF IMAGES OF A PRINTED POLYPROPYLENE RICE CAKES BAG FOR YOUR REFERENCE)
Updates

Project Deadline Extended
Reason: We want to provide the designers with NUTRITIONAL INFORMATION, Bar Code, Company information, Ingredients, important pointers, etc. to be incorporated into the design. We would like to provide a few more days in order to fully integrate the back & front text into the package design in order to attain a perfectly balanced and well presented package. So far we have received some very interesting and highly viable proposals and we would like to provide the designers the necessary text information in order to have a complete, fully designed, great-looking package. We feel that with the extension the final design can be completed and we can have an opportunity to review, incorporate/change/modify any details before choosing the final design. Great designs have been submitted and we will definitely choose one before the newly proposed deadline. Thanks to all!

Target Market(s)

Although the concept of RICE CAKES might very well have its origins in ASIA the idea is to create a design (logo & pack) that will convey a message to the end consumer that our brand name stands for "FRESHNESS", "HEALTHY", "NATURE'S BEST", "TOP GRAINS", "GOODNESS", in short if you consume are products "IT IS GOOD FOR YOU!" (not only for people who love oriental food). We would like to have a product image that says "Hey! This looks Healthy & Tasty" (non-fattening, yummy and good!)

When you buy a pack of GRANOLAS what do you think about? What do you believe it is that you are buying? Good, Healthy Stuff? Good Tasting? Good for you? That's the idea!

Besides Rice Cakes are super light, fluffy, crunchy and easy to digest that it makes it a great Snack for everyone! Kids & Adults!

We need the full complete design of the actual bag (where the Rice Cakes will be packed) in order to start production of the bags right.

Industry/Entity Type

Plastic

Requirements
Must have
• We already have a local company in Mexico City that makes printed polypropylene bags. They are only waiting for the bag design in order to print the 20cms x 30cms bags.
Kindly consider that on the back Nutritional Information will be needed as well as a BarCode, company information, some bullets (pointing to the most important benefits of the product), etc. We will provide all the text information.
Nice to have
• Kindly take a look at the newly uploaded images from "TORVE" Rice Cake packages. They are a good example of how to accomplish a great looking design using only 4 colors (which saves a lot in printing costs)
Should not have
• We do NOT want to have a design that says "This is ORIENTAL food". We don't want it to appear like "Sushi Rice" or "Japanese food", etc.

```html
<!DOCTYPE html>
<html lang="en">
<head>
<meta charset="utf-8">
<title>Harvel Foods Lightly Salted Rice Cakes – Bag Front</title>
<link rel="stylesheet" href="https://fonts.googleapis.com/css2?family=Cormorant+Garamond:ital,wght@1,500;1,600&family=Open+Sans:wght@400&family=Roboto+Condensed:wght@400;700&display=swap">
<style>
  :root {
    --sky-deep: #5cc6dc;
    --sky-light: #a9e2f6;
    --sand: #dfbd9f;
    --gold-line: #d8b36a;
    --mist: #e7ecea;
    --leaf-mist: #c9d8b6;
    --ice: #dcedf9;
    --ink: #4f4f4f;
    --ink-dark: #3a3a3a;
    --orange: #f2a23a;
    --white: #ffffff;
    --crisp-light: #e4dccd;
    --crisp: #cfc2ab;
  }
  html, body {
    margin: 0;
    padding: 0;
    width: 800px;
    height: 1200px;
    overflow: hidden;
    background: var(--white);
  }
  .bag {
    position: relative;
    width: 800px;
    height: 1200px;
    overflow: hidden;
    background: var(--white);
  }
  .sky-top {
    position: absolute;
    left: 0; top: 38px;
    width: 800px; height: 232px;
    background: linear-gradient(90deg, var(--sky-deep), var(--sky-light) 50%, var(--sky-deep));
  }
  .brand-band {
    position: absolute;
    left: 0; top: 270px;
    width: 800px; height: 125px;
    background: var(--sand);
    border-top: 3px solid var(--gold-line);
    border-bottom: 3px solid var(--gold-line);
    box-sizing: border-box;
  }
  .band-tag {
    position: absolute;
    top: 52px;
    font-family: "Open Sans", sans-serif;
    font-size: 20px;
    letter-spacing: 0.5px;
    color: var(--white);
  }
  .band-tag--left { left: 20px; }
  .band-tag--right { right: 58px; }
  .brand-name {
    position: absolute;
    left: 0; right: 0; top: 58px;
    text-align: center;
    font-family: "Roboto Condensed", sans-serif;
    font-weight: 700;
    font-size: 46px;
    line-height: 52px;
    letter-spacing: 1px;
    color: var(--white);
  }
  .brand-dot {
    display: inline-block;
    width: 16px; height: 16px;
    border-radius: 50%;
    background: var(--white);
    margin-right: 12px;
    vertical-align: 8px;
  }
  .field-scene {
    position: absolute;
    left: 0; top: 395px;
    width: 800px; height: 485px;
    background:
      radial-gradient(ellipse at 15% 70%, #8fbf4a 0%, rgba(143,191,74,0) 35%),
      linear-gradient(180deg, var(--mist) 0%, var(--leaf-mist) 60%, #e4ead8 100%);
  }
  .flavor {
    position: absolute;
    left: 0; right: 0; top: 412px;
    text-align: center;
    font-family: "Cormorant Garamond", serif;
    font-style: italic;
    font-weight: 500;
    font-size: 66px;
    color: var(--ink);
    margin: 0;
  }
  .benefits {
    position: absolute;
    left: 578px; top: 512px;
    margin: 0;
    padding: 0 0 0 10px;
    list-style: none;
    border-left: 1px solid #9a9a9a;
    font-family: "Roboto Condensed", sans-serif;
    font-weight: 700;
    font-size: 15px;
    color: var(--ink);
  }
  .benefits li {
    height: 39px;
    line-height: 30px;
  }
  .gluten-band {
    position: absolute;
    left: 0; top: 880px;
    width: 800px; height: 62px;
    background: var(--ice);
  }
  .gluten-band span {
    position: absolute;
    left: 86px; top: 14px;
    font-family: "Open Sans", sans-serif;
    font-size: 26px;
    letter-spacing: 2px;
    color: var(--ink);
  }
  .sky-bottom {
    position: absolute;
    left: 0; top: 942px;
    width: 800px; height: 258px;
    background: linear-gradient(90deg, var(--sky-deep), var(--sky-light) 50%, var(--sky-deep));
  }
  .product-name {
    position: absolute;
    left: 0; top: 0;
    margin: 0;
    font-family: "Cormorant Garamond", serif;
    font-style: italic;
    font-weight: 600;
  }
  .product-name .word-rice {
    position: absolute;
    left: 100px; top: 942px;
    font-size: 100px;
    line-height: 100px;
    color: var(--ink);
    white-space: nowrap;
  }
  .product-name .word-cakes {
    position: absolute;
    left: 80px; top: 1000px;
    font-size: 150px;
    line-height: 150px;
    color: var(--white);
    -webkit-text-stroke: 2px var(--orange);
    paint-order: stroke fill;
    white-space: nowrap;
  }
  .window {
    position: absolute;
    left: 413px; top: 741px;
    width: 330px; height: 330px;
    border-radius: 50%;
    border: 8px solid var(--white);
    box-sizing: border-box;
    background: radial-gradient(circle at 40% 40%, var(--crisp-light), var(--crisp));
    box-shadow: 0 0 0 1px rgba(0,0,0,0.08);
  }
  .net-weight {
    position: absolute;
    right: 48px; top: 1124px;
    font-family: "Roboto Condensed", sans-serif;
    font-size: 25px;
    color: var(--ink-dark);
  }
</style>
</head>
<body>
  <main class="bag">
    <div class="sky-top"></div>

    <header class="brand-band">
      <span class="band-tag band-tag--left">NATURE'S BEST</span>
      <div class="brand-name"><span class="brand-dot"></span>HARVEL FOODS</div>
      <span class="band-tag band-tag--right">12 RICE CAKES</span>
    </header>

    <div class="field-scene" role="img" aria-label="Photograph of green rice stalks with ripe grain heads and a small bowl of sea salt on a soft misty background"></div>

    <h2 class="flavor">Lightly salted</h2>

    <ul class="benefits">
      <li>30 CALORIES PER SLICE</li>
      <li>NATURAL INGREDIENTS</li>
      <li>NO TRANS FAT</li>
      <li>NO PRESERVATIVES</li>
      <li>NO FOOD COLORS</li>
      <li>WHOLE GRAIN</li>
    </ul>

    <div class="gluten-band"><span>GLUTEN FREE</span></div>

    <div class="sky-bottom"></div>

    <h1 class="product-name">
      <span class="word-rice">rice</span>
      <span class="word-cakes">cakes</span>
    </h1>

    <div class="window" role="img" aria-label="Round product window showing the stacked rice cakes inside the bag"></div>

    <div class="net-weight">NET WT 3.5 OZ {100gr}</div>
  </main>
</body>
</html>
```